Heron Haulage needs Bussiness cards!

Our new trucking company needs business cards!
We need the same design with two different names and emails, everything else it's the same.
I have included our original logo so we can use it for the design.
Note: the logo to be used is the o e with the buffalo on the right side, next to the letters H and H.

Target Market(s)

Trucking, refrigerated transportation, freight

Industry/Entity Type

Business

Contact Information for Business Card

Card #1:
Marcus Whitfield
marcuswhitfield@heronhaulage.example
1-855-317-6094
(956)238-7160
4117 W. Larkin Ave.
Pharr, TX 78590
www.heronhaulage.example

Card#2:
Rosalba Quintero
rosalba@heronhaulage.example
1-855-317-6094
(956)238-7160
4117 W. Larkin Ave.
Pharr, TX 78590
www.heronhaulage.example

Font styles to use
Sans Serif

Colors
0655a3
ec1f27
ffffff

Requirements
Must have
• our logo
Nice to have
• roads on background,

```html
<!DOCTYPE html>
<html lang="en">
<head>
<meta charset="utf-8">
<title>Heron Haulage – Business Cards</title>
<link href="https://fonts.googleapis.com/css2?family=Roboto:wght@400;900&display=swap" rel="stylesheet">
<style>
  :root {
    --navy: #0b3b78;
    --blue: #0655a3;
    --red: #ec1f27;
    --white: #ffffff;
    --backdrop: #2b2b2d;
  }
  * { box-sizing: border-box; margin: 0; padding: 0; }
  html, body {
    width: 1200px; height: 950px; overflow: hidden;
    background: var(--backdrop);
    font-family: "Roboto", Arial, sans-serif;
  }
  .sheet {
    position: relative; width: 1200px; height: 950px;
    display: flex; flex-direction: column; align-items: center;
    justify-content: center; gap: 50px;
  }
  .card {
    position: relative; width: 700px; height: 400px;
    background: var(--white); overflow: hidden;
  }
  .brand {
    position: absolute; display: flex; align-items: center; gap: 14px;
  }
  .brand-dot {
    width: 34px; height: 34px; border-radius: 50%; background: var(--red);
    flex: none;
  }
  .brand-name {
    font-weight: 900; color: var(--navy); font-size: 52px;
    line-height: 1; letter-spacing: -0.5px; white-space: nowrap;
  }
  .card-front .brand { left: 50%; top: 50%; transform: translate(-50%, -50%); }
  .card-back .brand { left: 50%; top: 62px; transform: translateX(-50%); }
  .card-back .brand-name { font-size: 46px; }
  .card-back .brand-dot { width: 30px; height: 30px; }
  .band { position: absolute; inset: 0; width: 100%; height: 100%; }
  .holder {
    position: absolute; right: 30px; top: 178px; text-align: right;
    color: var(--white);
  }
  .holder-name { font-size: 24px; font-weight: 400; margin-bottom: 8px; }
  .holder-line { font-size: 14px; line-height: 1.45; opacity: .92; }
  .contact-list {
    position: absolute; left: 30px; bottom: 34px; list-style: none;
    color: var(--white); font-size: 15px;
  }
  .contact-list li { display: flex; align-items: center; gap: 10px; line-height: 1.7; }
  .contact-list svg { width: 15px; height: 15px; flex: none; }
</style>
</head>
<body>
<main class="sheet">
  <section class="card card-front" aria-label="Card front">
    <div class="brand">
      <span class="brand-dot"></span>
      <span class="brand-name">Heron Haulage</span>
    </div>
  </section>

  <section class="card card-back" aria-label="Card back">
    <svg class="band" viewBox="0 0 700 400" preserveAspectRatio="none" aria-hidden="true">
      <polygon points="700,112 700,138 60,268 0,276 0,270" fill="var(--red)"/>
      <polygon points="700,80 700,90 250,200 230,202" fill="var(--red)"/>
      <polygon points="620,110 640,108 180,236 160,238" fill="var(--red)"/>
      <polygon points="700,138 700,400 0,400 0,276" fill="var(--navy)"/>
    </svg>

    <div class="brand">
      <span class="brand-dot"></span>
      <span class="brand-name">Heron Haulage</span>
    </div>

    <div class="holder">
      <p class="holder-name">Marcus Whitfield</p>
      <p class="holder-line">marcuswhitfield@heronhaulage.example</p>
      <p class="holder-line">4117 W. Larkin Ave. Pharr, TX 78590</p>
    </div>

    <ul class="contact-list">
      <li>
        <svg viewBox="0 0 16 16" aria-hidden="true"><path fill="#fff" d="M2 5c0-2 1.5-3 6-3s6 1 6 3v1h-3V5H5v1H2zM4 7h8l2 7H2z"/></svg>
        1-855-317-6094
      </li>
      <li>
        <svg viewBox="0 0 16 16" aria-hidden="true"><rect x="4" y="1" width="8" height="14" rx="1.5" fill="none" stroke="#fff" stroke-width="1.6"/><circle cx="8" cy="12.5" r="1" fill="#fff"/></svg>
        (956)238-7160
      </li>
      <li>
        <svg viewBox="0 0 16 16" aria-hidden="true"><circle cx="8" cy="8" r="6.5" fill="none" stroke="#fff" stroke-width="1.5"/><path d="M1.5 8h13M8 1.5c-3 3.5-3 9.5 0 13M8 1.5c3 3.5 3 9.5 0 13" fill="none" stroke="#fff" stroke-width="1.2"/></svg>
        www.heronhaulage.example
      </li>
    </ul>
  </section>
</main>
</body>
</html>
```